I need a business card design for a new business based in South West Australia.
I specialize in residential window cleaning & general handyman maintenance.

Dale Marsh - 412 SILVER HAWK DETAILING
- Window Cleaning
- House Maintenance

```html
<!DOCTYPE html>
<html lang="en">
<head>
<meta charset="utf-8">
<title>Silver Hawk Detailing – Business Card</title>
<link rel="stylesheet" href="https://fonts.googleapis.com/css2?family=Lato:wght@400;700;900&display=swap">
<style>
  :root {
    --backdrop: #e9e4df;
    --card: #ffffff;
    --brand-blue: #1a4fa0;
    --band-blue-top: #1668c4;
    --band-blue-bottom: #0d4690;
    --accent-orange: #ff6a00;
    --ink-light: #ffffff;
  }
  * { margin: 0; padding: 0; box-sizing: border-box; }
  html, body {
    width: 1200px; height: 900px; overflow: hidden;
    background: var(--backdrop);
    font-family: "Lato", sans-serif;
  }
  .canvas { position: relative; width: 1200px; height: 900px; }
  .card {
    position: absolute; background: var(--card); overflow: hidden;
    box-shadow: 0 4px 14px rgba(0,0,0,.18);
  }
  .card--front { left: 77px; top: 34px; width: 589px; height: 364px; }
  .card--back { left: 388px; top: 505px; width: 566px; height: 352px; }
  .card__bands { position: absolute; inset: 0; }
  .brand { position: absolute; left: 0; right: 0; text-align: center; }
  .brand__name { color: var(--brand-blue); font-weight: 900; letter-spacing: .5px; white-space: nowrap; }
  .brand__tagline { color: var(--accent-orange); font-weight: 900; letter-spacing: .6px; white-space: nowrap; }
  .card--front .brand { top: 120px; left: 80px; right: 90px; }
  .card--front .brand__name { font-size: 29px; line-height: 34px; }
  .card--front .brand__tagline { font-size: 11.5px; line-height: 16px; }
  .card--back .brand { top: 200px; }
  .card--back .brand__name { font-size: 36px; line-height: 42px; }
  .card--back .brand__tagline { font-size: 14px; line-height: 20px; }
  .person {
    position: absolute; right: 319px; top: 234px; text-align: right;
    color: var(--ink-light);
  }
  .person__name { font-size: 24px; line-height: 30px; }
  .person__role { font-size: 17px; line-height: 22px; margin-bottom: 8px; }
  .person__address { font-size: 17px; line-height: 23px; }
  .contacts {
    position: absolute; left: 310px; top: 241px; list-style: none;
    color: var(--ink-light); font-size: 17px;
  }
  .contacts li { display: flex; align-items: center; height: 25px; }
  .contacts svg { width: 16px; height: 16px; margin-right: 7px; flex: none; }
</style>
</head>
<body>
<main class="canvas">
  <section class="card card--front" aria-label="Business card front">
    <svg class="card__bands" viewBox="0 0 589 364" aria-hidden="true">
      <defs>
        <linearGradient id="bandBlue" x1="0" y1="0" x2="0" y2="1">
          <stop offset="0" stop-color="var(--band-blue-top)"/>
          <stop offset="1" stop-color="var(--band-blue-bottom)"/>
        </linearGradient>
      </defs>
      <polygon points="0,195 400,195 380,220 0,220" fill="var(--accent-orange)"/>
      <polygon points="414,186 589,186 589,364 0,364 0,224 378,224" fill="url(#bandBlue)"/>
    </svg>
    <div class="brand">
      <div class="brand__name">SILVER HAWK DETAILING</div>
      <div class="brand__tagline">WINDOW CLEANING &amp; HOUSE MAINTENANCE</div>
    </div>
    <div class="person">
      <div class="person__name">Dale Marsh</div>
      <div class="person__role">Managing Director</div>
      <div class="person__address">27 Karri Lane, Busselton<br>WA Australia, 6280</div>
    </div>
    <ul class="contacts">
      <li><svg viewBox="0 0 16 16"><rect width="16" height="16" rx="3" fill="#fff"/><path d="M4 6h8v5H4z M6 4h4v2H6z" fill="var(--band-blue-bottom)"/></svg>08 9555 0142</li>
      <li><svg viewBox="0 0 16 16"><rect width="16" height="16" rx="3" fill="#fff"/><rect x="5" y="3" width="6" height="10" rx="1" fill="var(--band-blue-bottom)"/></svg>0400 555 318</li>
      <li><svg viewBox="0 0 16 16"><rect width="16" height="16" rx="3" fill="#fff"/><rect x="3" y="5" width="10" height="7" fill="var(--band-blue-bottom)"/><path d="M3 5l5 4 5-4" stroke="#fff" fill="none"/></svg>hello@silverhawk.au</li>
      <li><svg viewBox="0 0 16 16"><rect width="16" height="16" rx="3" fill="#fff"/><path d="M5 11l6-6 M4 8l-1 1a2 2 0 003 3l1-1 M12 8l1-1a2 2 0 00-3-3l-1 1" stroke="var(--band-blue-bottom)" stroke-width="1.6" fill="none"/></svg>www.silverhawk.au</li>
    </ul>
  </section>

  <section class="card card--back" aria-label="Business card back">
    <div class="brand">
      <div class="brand__name">SILVER HAWK DETAILING</div>
      <div class="brand__tagline">WINDOW CLEANING &amp; HOUSE MAINTENANCE</div>
    </div>
  </section>
</main>
</body>
</html>
```